hotel's Website

Hotels website redesign for reference pictures, logo etc see http://restwellharbour.co.uk/

1. 2-3 Special offers on the main page.
2. Booking calender
3. Location Map
4. Picture gallery.
5. Journeymarks reviews.
6. short description
7. Social Media sharing.
8 Phone number and address.

Industry/Entity Type

Hotel

Requirements
Must have
• 1. 2-3 Special offers on the main page.
2. Booking calender
3. Location Map
4. Picture gallery.
5. Journeymarks reviews.
6. short description
7. Social Media sharing.

```html
<!DOCTYPE html>
<html lang="en">
<head>
<meta charset="utf-8">
<title>Restwell Harbour – Hotel</title>
<link rel="stylesheet" href="https://fonts.googleapis.com/css2?family=Open+Sans:wght@400;600;700&family=Noto+Serif:wght@400;700&display=swap">
<style>
:root{
  --maroon:#6a0d14;
  --maroon-dark:#4a070c;
  --red:#7c0f16;
  --blue:#3f87b8;
  --blue-light:#c6ddee;
  --blue-pale:#dce9f3;
  --green:#4d8a5e;
  --paper:#efece5;
  --paper-2:#e6e3de;
  --ink:#333;
  --muted:#666;
  --footer:#1e1e1e;
  --caption:#7d736b;
  --plum:#3d2a31;
  --white:#fff;
}
*{box-sizing:border-box;margin:0;padding:0}
html,body{width:1200px;height:2824px;overflow:hidden}
body{font-family:"Open Sans",Arial,sans-serif;color:var(--ink);background:var(--paper)}
.page{position:relative;width:1200px;height:2824px;overflow:hidden;background:var(--paper)}
.abs{position:absolute}
.serif{font-family:"Noto Serif",Georgia,serif}

/* top bar */
.topbar{left:0;top:0;width:1200px;height:30px;background:var(--maroon);color:#fff;font-size:11px;z-index:5}
.topbar .contact-item{position:absolute;top:0;height:30px;display:flex;align-items:center;gap:8px}
.topbar .ico{width:22px;height:22px;background:rgba(255,255,255,.2);display:flex;align-items:center;justify-content:center}
.social{position:absolute;top:0;display:flex;gap:6px}
.social span{width:26px;height:30px;display:block}
.social .s1{background:#3c9ad0}.social .s2{background:#3a5b9a}.social .s3{background:#c94a3a}
.location-link{position:absolute;right:20px;top:0;height:30px;display:flex;align-items:center;gap:10px;font-size:11px}

/* hero */
.hero{left:0;top:30px;width:1200px;height:316px;background:linear-gradient(100deg,#c9c3b8 0%,#9b958c 30%,#6e6a64 55%,#a59c8e 80%,#c7c0b3 100%)}
.navbar{left:0;top:30px;width:1200px;height:62px;background:rgba(255,255,255,.72);z-index:4}
.brand{left:256px;top:30px;width:58px;height:64px;background:var(--blue);z-index:6;color:#fff;font-family:"Open Sans",sans-serif;font-weight:700;font-size:10px;display:flex;align-items:flex-end;justify-content:center;text-align:center;padding-bottom:6px;line-height:1.2}
.nav{left:334px;top:56px;z-index:6;display:flex;gap:26px;font-size:11px;font-weight:600;color:#3a3a3a;text-transform:uppercase}
.nav .active{color:var(--blue)}
.hero-slide-title{left:256px;top:134px;width:324px;height:46px;background:rgba(63,135,184,.82);color:#fff;font-size:26px;line-height:46px;padding-left:24px;z-index:3}
.hero-slide-sub{left:304px;top:186px;width:276px;height:24px;background:rgba(30,20,20,.8);color:#fff;font-size:14px;line-height:24px;padding-left:10px;z-index:3}
.btn-red{background:var(--red);color:#fff;border-bottom:3px solid var(--maroon-dark)}
.hero-cta{left:452px;top:216px;width:128px;height:40px;font-size:20px;text-align:center;line-height:38px;z-index:3}
.slider-arrow{top:144px;width:36px;height:50px;background:var(--blue);z-index:3;display:flex;align-items:center;justify-content:center}

/* calendar */
.calendar{left:256px;top:234px;width:156px;height:164px;background:#eeeeee;border:1px solid #bbb;z-index:7;font-size:8px}
.cal-head{height:18px;background:#444;color:#fff;display:flex;justify-content:space-between;align-items:center;padding:0 8px;font-size:9px}
.cal-grid{display:grid;grid-template-columns:repeat(7,1fr);gap:2px;padding:4px}
.cal-grid span{height:17px;display:flex;align-items:center;justify-content:center;background:#fff;color:#444}
.cal-grid .dow{background:none;height:10px;font-size:6px;color:#777}
.cal-grid .out{color:#aaa;background:#f6f6f6}
.cal-grid .sel{background:var(--blue);color:#fff}

/* booking bar */
.booking{top:386px;height:34px;z-index:6;display:flex;align-items:center;font-size:12px;color:#fff}
.field{position:absolute;top:0;height:34px;background:var(--blue);display:flex;align-items:center;justify-content:space-between;padding-left:18px;border:1px solid #2f6d97}
.field .addon{width:36px;height:32px;background:#3374a1;display:flex;align-items:center;justify-content:center}
.check{position:absolute;top:0;left:530px;width:150px;height:34px;background:var(--maroon);border:1px solid #3f060a;display:flex;align-items:center;justify-content:center;font-size:12px}

/* offers */
.offer{top:462px;width:192px;text-align:center}
.offer .photo{width:192px;height:170px;border:5px solid #fff;box-shadow:0 3px 6px rgba(0,0,0,.25)}
.offer .pin{width:12px;height:12px;border:2px solid #555;border-radius:50%;margin:-4px auto 0;background:#fff;position:relative}
.offer h3{font-family:"Noto Serif",Georgia,serif;color:var(--green);font-size:16px;line-height:20px;margin-top:4px;font-weight:700}
.offer p{font-size:11px;line-height:16px;color:#444;margin:8px 0 0}
.btn-blue{background:var(--blue);color:#fff;border-bottom:3px solid #2c6690;display:flex;align-items:center;justify-content:center;gap:14px;font-weight:700;font-size:16px}
.offer .btn-blue{width:124px;height:32px;margin:12px auto 0}

/* about band */
.about{left:0;top:786px;width:1200px;height:442px;background:radial-gradient(ellipse at 50% 70%,#5a3c44 0%,#3d2a31 55%,#2b1d22 100%)}
.about p{position:absolute;left:266px;top:52px;width:662px;color:#f3eef0;font-size:22.5px;line-height:32px;letter-spacing:.5px}
.book-big{left:414px;top:310px;width:336px;height:76px;font-size:38px;font-weight:600;display:flex;align-items:center;justify-content:center;gap:18px;border-bottom:5px solid var(--maroon-dark);letter-spacing:1px}

/* reviews */
.reviews-head{left:256px;top:1250px;width:688px;height:46px;background:var(--blue);border:2px solid #2f6d97;display:flex;align-items:center;color:#fff;font-family:"Noto Serif",Georgia,serif;font-weight:700;font-size:20px;letter-spacing:.5px}
.reviews-head .badge{width:60px;height:42px;background:#fff;margin:0 12px 0 4px;border-radius:4px}
.review{left:270px;width:674px}
.review .stars{position:absolute;left:0;top:0;color:#e6a018;font-size:14px;letter-spacing:1px}
.review .name{position:absolute;left:76px;top:0;font-size:15px;font-weight:700;color:#333}
.review .date{position:absolute;left:76px;top:22px;font-size:9px;color:#888}
.review p{position:absolute;left:154px;top:18px;width:520px;font-size:10px;line-height:15px;color:#666}
.divider{left:270px;top:1394px;width:674px;height:2px;background:#7e1f23}
.view-all{left:740px;top:1472px;width:176px;height:38px;font-size:18px;display:flex;align-items:center;justify-content:center;gap:12px;border-radius:3px}

/* events & videos */
.sec-label{height:28px;background:var(--blue);color:#fff;font-family:"Noto Serif",Georgia,serif;font-weight:700;font-size:17px;line-height:28px;padding-left:8px}
.event{left:256px;width:342px;background:var(--blue-light);border:1px solid #aac7dc}
.event .date{position:absolute;left:6px;top:10px;width:40px;text-align:center;font-size:12px}
.event .date .d{background:#fff;height:22px;line-height:22px}
.event .date .m{background:var(--blue);color:#fff;height:14px;line-height:14px;font-size:9px;font-weight:700}
.event .thumb{position:absolute;left:56px;top:10px;width:70px;height:76px;border:3px solid #fff}
.event h4{position:absolute;left:132px;top:6px;font-size:13px;font-weight:400;color:#333}
.event .meta{position:absolute;left:132px;top:26px;font-size:8px;color:#888}
.event p{position:absolute;left:132px;top:42px;width:200px;font-size:8.5px;line-height:12px;color:#555}
.event .more{position:absolute;right:14px;bottom:6px;font-size:8.5px;color:#444}
.video{left:618px;top:1604px;width:326px;height:178px;background:linear-gradient(180deg,#1d1733 0%,#2a2050 55%,#0d0d18 100%)}
.video .title{position:absolute;left:8px;top:6px;color:#fff;font-size:11px}
.video .play{position:absolute;left:140px;top:72px;width:46px;height:32px;background:#c8241f;border-radius:8px;display:flex;align-items:center;justify-content:center}
.video .controls{position:absolute;left:0;bottom:0;width:100%;height:16px;background:#111}
.video .controls i{position:absolute;left:40px;top:6px;width:270px;height:3px;background:#444}
.video .controls b{position:absolute;left:40px;top:6px;width:30px;height:3px;background:#c8241f}

/* gallery */
.gallery{left:0;top:1840px;width:1200px;height:652px;background:var(--paper-2)}
.gallery h2{position:absolute;left:0;top:28px;width:1200px;text-align:center;font-family:"Noto Serif",Georgia,serif;color:var(--maroon);font-size:30px;letter-spacing:2px;display:flex;align-items:center;justify-content:center;gap:14px}
.g-item{width:220px;height:184px;border-radius:3px;overflow:hidden}
.g-item .img{width:100%;height:144px}
.g-item .cap{height:40px;background:var(--caption);color:#fff;padding:4px 8px}
.g-item .cap b{display:block;font-weight:400;font-size:15px;line-height:18px}
.g-item .cap span{display:block;font-size:9px;line-height:12px;color:#eee}
.g-item.active .cap{background:var(--blue)}
.zoom{position:absolute;left:90px;top:58px;width:38px;height:38px;border-radius:50%;background:#222;display:flex;align-items:center;justify-content:center}
.room-a{background:linear-gradient(160deg,#b08a55,#6d4028 55%,#c9c0b2)}
.room-b{background:linear-gradient(160deg,#e6dcc0,#c9b78f 60%,#8b7255)}
.room-c{background:linear-gradient(160deg,#a68a6c,#6e3b2b 55%,#d8cfc0)}

/* tweet band */
.tweet{left:0;top:2492px;width:1200px;height:66px;background:#4a8cc0;color:#fff;font-size:12px;display:flex;align-items:center}
.tweet .dot{position:absolute;left:260px;top:17px;width:32px;height:32px;border-radius:50%;background:#fff;opacity:.9}
.tweet p{position:absolute;left:324px;top:24px}

/* footer */
.footer{left:0;top:2558px;width:1200px;height:230px;background:var(--footer);border-top:8px solid var(--red);color:#ddd}
.footer h5{font-family:"Noto Serif",Georgia,serif;font-size:13px;font-weight:700;letter-spacing:1px;color:#eee;position:absolute;top:46px}
.footer .col{position:absolute;top:72px;font-size:11px;line-height:18px;color:#eee}
.footer ul{list-style:none}
.footer ul li{font-size:10px;line-height:18px;color:#ccc}
.attr-grid{display:grid;grid-template-columns:repeat(3,46px);gap:14px 8px}
.attr-grid span{height:46px;border:2px solid var(--blue)}
.f-more{position:absolute;top:192px;width:76px;height:26px;background:var(--maroon);color:#fff;font-size:12px;display:flex;align-items:center;justify-content:center;gap:8px;border-bottom:2px solid #3a0508}
.contact-row{display:flex;gap:8px;font-size:10px;line-height:14px;margin-bottom:8px;color:#ccc}
.bottombar{left:0;top:2788px;width:1200px;height:36px;background:var(--maroon);color:#d9b9bb;font-size:10px}
.bottombar p{position:absolute;left:256px;top:11px}
.bottom-social{position:absolute;left:760px;top:8px;display:flex;gap:18px}
.bottom-social span{width:18px;height:18px;border-radius:50%;background:rgba(255,255,255,.35)}
</style>
</head>
<body>
<div class="page">

  <!-- Top bar -->
  <div class="abs topbar">
    <div class="contact-item" style="left:256px">
      <span class="ico"><svg width="12" height="12" viewBox="0 0 24 24"><path fill="#fff" d="M6.6 10.8a15 15 0 0 0 6.6 6.6l2.2-2.2c.3-.3.7-.4 1-.2 1.1.4 2.3.6 3.6.6.6 0 1 .4 1 1V20c0 .6-.4 1-1 1A17 17 0 0 1 3 4c0-.6.4-1 1-1h3.5c.6 0 1 .4 1 1 0 1.3.2 2.5.6 3.6.1.3 0 .7-.2 1z"/></svg></span>
      +44 (0) 20 7946 0321
    </div>
    <div class="contact-item" style="left:398px">
      <span class="ico"><svg width="12" height="10" viewBox="0 0 24 18"><rect x="1" y="1" width="22" height="16" fill="none" stroke="#fff" stroke-width="2"/><path d="M1 1l11 9 11-9" fill="none" stroke="#fff" stroke-width="2"/></svg></span>
      info@restwellharbour.co.uk
    </div>
    <div class="social" style="left:758px"><span class="s1"></span><span class="s2"></span><span class="s3"></span></div>
    <div class="location-link">Click Here To View Location
      <svg width="30" height="12" viewBox="0 0 30 12"><path d="M0 6h18M14 2l4 4-4 4" stroke="#8fb8d8" stroke-width="2" fill="none"/><path d="M25 1a4 4 0 0 1 4 4c0 3-4 7-4 7s-4-4-4-7a4 4 0 0 1 4-4z" fill="#8fb8d8"/></svg>
    </div>
  </div>

  <!-- Hero -->
  <div class="abs hero" role="img" aria-label="Photo of a smiling couple on a scooter in a London street of white townhouses"></div>
  <div class="abs navbar"></div>
  <div class="abs brand">Restwell Harbour</div>
  <nav class="abs nav">
    <span>Home</span><span class="active">Bedrooms</span><span>Attractions</span><span>London Events</span><span>Special Offers</span><span>Photos</span><span>Videos</span><span>Contact</span>
    <svg width="12" height="12" viewBox="0 0 24 24"><circle cx="10" cy="10" r="7" fill="none" stroke="#333" stroke-width="3"/><path d="M15 15l7 7" stroke="#333" stroke-width="3"/></svg>
  </nav>
  <div class="abs slider-arrow" style="left:0"><svg width="12" height="20" viewBox="0 0 12 20"><path d="M10 2L2 10l8 8" stroke="#fff" stroke-width="3" fill="none"/></svg></div>
  <div class="abs slider-arrow" style="left:1164px"><svg width="12" height="20" viewBox="0 0 12 20"><path d="M2 2l8 8-8 8" stroke="#fff" stroke-width="3" fill="none"/></svg></div>
  <div class="abs hero-slide-title">Lorem ipsum dolor sit</div>
  <div class="abs hero-slide-sub">Sed ut perspiciatis unde omnis iste natus</div>
  <div class="abs hero-cta btn-red">Click Here</div>

  <!-- Booking calendar -->
  <div class="abs calendar">
    <div class="cal-head"><span>◂</span><span>December 2013</span><span>▸</span></div>
    <div class="cal-grid">
      <span class="dow">MON</span><span class="dow">TUE</span><span class="dow">WED</span><span class="dow">THU</span><span class="dow">FRI</span><span class="dow">SAT</span><span class="dow">SUN</span>
      <span class="out">25</span><span class="out">26</span><span class="out">27</span><span class="out">28</span><span class="out">29</span><span class="out">30</span><span>1</span>
      <span>2</span><span>3</span><span>4</span><span class="sel">5</span><span>6</span><span>7</span><span>8</span>
      <span>9</span><span>10</span><span>11</span><span>12</span><span>13</span><span>14</span><span>15</span>
      <span>16</span><span>17</span><span>18</span><span>19</span><span>20</span><span>21</span><span>22</span>
      <span>23</span><span>24</span><span>25</span><span>26</span><span>27</span><span>28</span><span>29</span>
      <span>30</span><span>31</span><span class="out">1</span><span class="out">2</span><span class="out">3</span><span class="out">4</span><span class="out">5</span>
    </div>
  </div>

  <!-- Booking bar -->
  <div class="abs booking" style="left:264px;width:680px">
    <div class="field" style="left:0;width:116px">Arrive<span class="addon"><svg width="14" height="12" viewBox="0 0 14 12"><rect x="1" y="2" width="12" height="9" fill="none" stroke="#fff" stroke-width="1.5"/><path d="M1 5h12" stroke="#fff"/></svg></span></div>
    <div class="field" style="left:136px;width:116px">Depart<span class="addon"><svg width="14" height="12" viewBox="0 0 14 12"><rect x="1" y="2" width="12" height="9" fill="none" stroke="#fff" stroke-width="1.5"/><path d="M1 5h12" stroke="#fff"/></svg></span></div>
    <div class="field" style="left:288px;width:108px">Guests<span class="addon">1</span></div>
    <div class="field" style="left:412px;width:96px">Room<span class="addon" style="width:40px">▭</span></div>
    <div class="check">Check Availability</div>
  </div>

  <!-- Special offers -->
  <div class="abs offer" style="left:258px">
    <div class="photo" role="img" aria-label="Photo of a woman in a spa wrap against a tiled wall" style="background:linear-gradient(135deg,#c58a5e,#8e5a4a 50%,#d8b58e)"></div>
    <div class="pin"></div>
    <h3>25% off on Spa<br>Treatments</h3>
    <p>Stay with us and get 25% off on<br>Spa Treatments.</p>
    <div class="btn-blue"><svg width="16" height="16" viewBox="0 0 16 16"><path d="M6 2H2v12h12v-4M9 2h5v5M14 2L7 9" stroke="#fff" stroke-width="2" fill="none"/></svg>Get it</div>
  </div>
  <div class="abs offer" style="left:500px">
    <div class="photo" role="img" aria-label="Photo of a lit shopping arcade window display" style="background:linear-gradient(135deg,#4a3a4e,#a1523e 50%,#2e3a5a)"></div>
    <div class="pin"></div>
    <h3>Shopping in<br>London</h3>
    <p>For the ultimate discount sales<br>shopping London is always ...</p>
    <div class="btn-blue"><svg width="16" height="16" viewBox="0 0 16 16"><path d="M6 2H2v12h12v-4M9 2h5v5M14 2L7 9" stroke="#fff" stroke-width="2" fill="none"/></svg>Shop Now</div>
  </div>
  <div class="abs offer" style="left:750px">
    <div class="photo" role="img" aria-label="Photo of a small white hire car parked on a street" style="background:linear-gradient(160deg,#b9c1c7,#eef0f1 45%,#6f777d)"></div>
    <div class="pin"></div>
    <h3>Low Cost<br>Car Hire</h3>
    <p>Driving in central London –<br>Hire a car</p>
    <div class="btn-blue"><svg width="16" height="16" viewBox="0 0 16 16"><path d="M6 2H2v12h12v-4M9 2h5v5M14 2L7 9" stroke="#fff" stroke-width="2" fill="none"/></svg>Book Now</div>
  </div>

  <!-- About band -->
  <section class="abs about" role="img" aria-label="Photo of a hotel bedroom with a double bed and bedside lamps">
    <p>Our tastefully appointed four storey building is comprised of three attractive Georgian style townhouses – beautifully renovated and continuously maintained to provide comfort as well as stylish decor and useful amenities in all rooms. Our Hotel is a non smoking hotel</p>
    <div class="abs book-big btn-red">Book Now
      <svg width="34" height="30" viewBox="0 0 24 22"><path d="M1 10L23 1l-5 20-6-7-5 5v-7z" fill="#fff"/></svg>
    </div>
  </section>

  <!-- Reviews -->
  <div class="abs reviews-head"><span class="badge"></span>SEE WHAT &nbsp;VISTORS ARE WRITING IN JOURNEYMARKS</div>
  <div class="abs review" style="top:1310px">
    <span class="stars">★★★★</span>
    <span class="name">John Doe</span>
    <span class="date">Nov 26, 2013</span>
    <p>Lorem ipsum dolor sit amet, consectetur adipisicing elit, sed do eiusmod tempor incididunt ut labore et dolore magna aliqua. Ut enim ad minim veniam, quis nostrud exercitation ullamco laboris nisi ut aliquip ex ea commodo consequat.</p>
  </div>
  <div class="abs divider"></div>
  <div class="abs review" style="top:1418px">
    <span class="stars">★★★★</span>
    <span class="name">John Doe</span>
    <span class="date">Nov 26, 2013</span>
    <p>Lorem ipsum dolor sit amet, consectetur adipisicing elit, sed do eiusmod tempor incididunt ut labore et dolore magna aliqua. Ut enim ad minim veniam, quis nostrud exercitation ullamco laboris nisi ut aliquip ex ea commodo consequat.</p>
  </div>
  <div class="abs view-all btn-red">VIEW ALL <span style="width:34px;height:20px;border-radius:10px;background:#fff;display:block"></span></div>

  <!-- Latest events -->
  <div class="abs sec-label" style="left:252px;top:1538px;width:218px">LATEST EVENTS</div>
  <div class="abs event" style="top:1580px;height:122px">
    <div class="date"><div class="d">01</div><div class="m">NOV</div></div>
    <div class="thumb" role="img" aria-label="Photo of guardsmen in red uniforms" style="background:linear-gradient(160deg,#8a2a2a,#3a2c2c)"></div>
    <h4>Lorem ipsum dolor</h4>
    <span class="meta">10 Comments</span>
    <p>Neque porro quisquam est, qui dolorem ipsum quia dolor sit amet, consectetur, adipisci velit, sed quia non numquam eius modi tempora incidunt ut labore et dolore magnam aliquam</p>
    <span class="more">Read More ➜</span>
  </div>
  <div class="abs event" style="top:1706px;height:112px">
    <div class="date"><div class="d">01</div><div class="m">NOV</div></div>
    <div class="thumb" role="img" aria-label="Photo of a colourful carnival costume" style="background:linear-gradient(160deg,#d23c6a,#3a6fc0 60%,#e6b23a)"></div>
    <h4>At vero eos et accusamus</h4>
    <span class="meta">8 Comments</span>
    <p>Neque porro quisquam est, qui dolorem ipsum quia dolor sit amet, consectetur, adipisci velit, sed quia non numquam eius modi tempora incidunt ut labore et dolore magnam</p>
    <span class="more">Read More ➜</span>
  </div>

  <!-- Latest videos -->
  <div class="abs sec-label" style="left:618px;top:1538px;width:218px">LATEST VIDEOS</div>
  <div class="abs" style="left:880px;top:1546px;font-size:11px;color:#333">View all ➜</div>
  <div class="abs video" role="img" aria-label="Video still of a lit Ferris wheel and Christmas market at night">
    <span class="title">2013 Restwell Harbour London Event1</span>
    <span class="play"><svg width="14" height="16" viewBox="0 0 14 16"><path d="M1 1l12 7-12 7z" fill="#fff"/></svg></span>
    <div class="controls"><i></i><b></b></div>
  </div>

  <!-- Gallery -->
  <section class="abs gallery">
    <h2><svg width="26" height="26" viewBox="0 0 26 26"><circle cx="13" cy="13" r="13" fill="#3f87b8"/><ellipse cx="13" cy="13" rx="8" ry="5" fill="none" stroke="#fff" stroke-width="2"/><circle cx="13" cy="13" r="2.5" fill="#fff"/></svg>GALLERY</h2>
    <div class="abs g-item active" style="left:256px;top:116px">
      <div class="img room-a" role="img" aria-label="Photo of a hotel room with a red-covered bed"></div>
      <span class="zoom"><svg width="16" height="16" viewBox="0 0 24 24"><circle cx="10" cy="10" r="7" fill="none" stroke="#fff" stroke-width="3"/><path d="M15 15l7 7" stroke="#fff" stroke-width="3"/></svg></span>
      <div class="cap"><b>Lorem Ipsum</b><span>Sed ut perspiciatis unde omnis</span></div>
    </div>
    <div class="abs g-item" style="left:490px;top:116px">
      <div class="img room-b" role="img" aria-label="Photo of a breakfast bar with high stools"></div>
      <div class="cap"><b>Lorem Ipsum</b><span>Sed ut perspiciatis unde omnis</span></div>
    </div>
    <div class="abs g-item" style="left:724px;top:116px">
      <div class="img room-c" role="img" aria-label="Photo of a twin bedroom with patterned bedspreads"></div>
      <div class="cap"><b>Lorem Ipsum</b><span>Sed ut perspiciatis unde omnis</span></div>
    </div>
    <div class="abs g-item" style="left:256px;top:318px">
      <div class="img room-a" role="img" aria-label="Photo of a double bedroom with a yellow headboard"></div>
      <div class="cap"><b>Lorem Ipsum</b><span>Sed ut perspiciatis unde omnis</span></div>
    </div>
    <div class="abs g-item" style="left:490px;top:318px">
      <div class="img room-b" role="img" aria-label="Photo of a breakfast bar with high stools"></div>
      <div class="cap"><b>Lorem Ipsum</b><span>Sed ut perspiciatis unde omnis</span></div>
    </div>
    <div class="abs g-item" style="left:724px;top:318px">
      <div class="img room-c" role="img" aria-label="Photo of a twin bedroom with patterned bedspreads"></div>
      <div class="cap"><b>Lorem Ipsum</b><span>Sed ut perspiciatis unde omnis</span></div>
    </div>
  </section>

  <!-- Social feed band -->
  <div class="abs tweet">
    <span class="dot"></span>
    <p>Lorem ipsum dolor sit amet, consectetur adipisicing elit, sed do eiusmod tempor incididunt ut labore</p>
  </div>

  <!-- Footer -->
  <footer class="abs footer">
    <h5 style="left:256px">ABOUT US</h5>
    <div class="col" style="left:256px;width:160px;line-height:17px">Sed ut perspiciatis unde omnis iste natus error sit voluptatem accusantium doloremque laudantium, totam rem aperiam, eaque ipsa quae ab illo inventore veritatis et quasi.</div>
    <span class="f-more" style="left:346px">More <svg width="12" height="10" viewBox="0 0 12 10"><path d="M1 5h9M7 2l3 3-3 3" stroke="#fff" stroke-width="2" fill="none"/></svg></span>

    <h5 style="left:442px;color:#777">ATTRACTIONS</h5>
    <div class="col attr-grid" style="left:442px">
      <span role="img" aria-label="Photo of a theatre sign" style="background:#c9a23a"></span>
      <span role="img" aria-label="Photo of a Ferris wheel at night" style="background:#2a3a7a"></span>
      <span role="img" aria-label="Photo of a city street" style="background:#c47a3a"></span>
      <span role="img" aria-label="Photo of a guarded gate" style="background:#8a6a52"></span>
      <span role="img" aria-label="Photo of a bridge at dusk" style="background:#3a4a8a"></span>
      <span role="img" aria-label="Photo of a parade" style="background:#7a8ab0"></span>
    </div>
    <span class="f-more" style="left:520px">More <svg width="12" height="10" viewBox="0 0 12 10"><path d="M1 5h9M7 2l3 3-3 3" stroke="#fff" stroke-width="2" fill="none"/></svg></span>

    <h5 style="left:620px">FROM OUR BLOG</h5>
    <ul class="col" style="left:620px">
      <li>| Lorem ipsum dolor sit amet</li>
      <li>| Adipiscing elit, sed do</li>
      <li>| Adipiscing elit, sed do</li>
      <li>| Incididunt ut labore et dolore</li>
      <li>| Quis nostrud exercitation</li>
    </ul>

    <h5 style="left:788px">CONTACT</h5>
    <div class="col" style="left:788px;width:170px">
      <div class="contact-row"><svg width="10" height="12" viewBox="0 0 10 12"><path d="M5 0a4 4 0 0 1 4 4c0 3-4 8-4 8S1 7 1 4a4 4 0 0 1 4-4z" fill="#bbb"/></svg><span>42 Mariner Row, Harbourside<br>London SE1 4QX</span></div>
      <div class="contact-row"><svg width="12" height="10" viewBox="0 0 24 18"><rect x="1" y="1" width="22" height="16" fill="none" stroke="#bbb" stroke-width="2"/><path d="M1 1l11 9 11-9" fill="none" stroke="#bbb" stroke-width="2"/></svg><span>stay@restwellharbour.co.uk</span></div>
      <div class="contact-row"><svg width="10" height="10" viewBox="0 0 24 24"><path fill="#bbb" d="M6.6 10.8a15 15 0 0 0 6.6 6.6l2.2-2.2c.3-.3.7-.4 1-.2 1.1.4 2.3.6 3.6.6.6 0 1 .4 1 1V20c0 .6-.4 1-1 1A17 17 0 0 1 3 4c0-.6.4-1 1-1h3.5c.6 0 1 .4 1 1 0 1.3.2 2.5.6 3.6.1.3 0 .7-.2 1z"/></svg><span>+ 44 (0) 20 7946 0188<br>Fax + 44 (0) 20 7946 0199</span></div>
    </div>
  </footer>

  <div class="abs bottombar">
    <p>Copyright 2013 Restwell Harbour UK</p>
    <div class="bottom-social"><span></span><span></span><span></span></div>
  </div>

</div>
</body>
</html>
```